Website Design for recruiting company

We need a homepage mockup for a recruiting company focused on the legal industry. Use your creative talent to come up with something visually appeal and professional for this web-site.

We'd really like to see the maze from the logo incorporated into the design somehow. Please use the website mockup provided as inspiration for this project. We really like the layout and photos!

Target Market(s)

lawyers

Industry/Entity Type

Legal

Number of Pages Required

1 page

Font styles to use
Sans Serif

```html
<!DOCTYPE html>
<html lang="en">
<head>
<meta charset="utf-8">
<title>Harborline Legal Search — Home</title>
<link rel="stylesheet" href="https://fonts.googleapis.com/css2?family=Poppins:wght@400;500;600;700&family=Hind:wght@400;500;600&display=swap">
<style>
:root{
  --plum:#5e5062;
  --plum-dark:#4d4151;
  --ink:#2b2b2b;
  --text:#3a3a3a;
  --muted:#555;
  --line:#e3e1e4;
  --footer-bg:#f4f2f4;
  --white:#fff;
}
*{margin:0;padding:0;box-sizing:border-box}
html,body{width:1200px;height:3483px;overflow:hidden}
body{position:relative;background:var(--white);font-family:'Hind',sans-serif;color:var(--text)}
.abs{position:absolute}
.heading{font-family:'Poppins',sans-serif;font-weight:700;color:var(--ink);letter-spacing:-.3px}
.rule{position:absolute;height:3px;background:var(--plum)}

/* hero */
.hero{left:0;top:0;width:1200px;height:660px;background:linear-gradient(115deg,#dfe3e8 0%,#b9c1cb 30%,#7d8590 52%,#c7ccd2 70%,#e9ebee 100%)}
.brand{left:132px;top:22px;display:flex;align-items:center;gap:16px}
.brand-dot{width:108px;height:108px;border-radius:50%;background:var(--plum);border:7px solid #cfd6c8}
.brand-name{font-family:'Hind',sans-serif;font-size:20px;color:var(--muted);margin-top:4px}
.nav{left:505px;top:32px;display:flex;gap:26px;font-family:'Poppins',sans-serif;font-weight:500;font-size:14px;color:var(--ink)}
.nav a{color:inherit;text-decoration:none}
.nav .active{color:var(--plum);text-decoration:underline;text-underline-offset:4px}
.search-btn{left:1033px;top:22px;width:34px;height:34px;border-radius:50%;background:var(--plum);display:flex;align-items:center;justify-content:center}
.hero-caption{left:138px;top:444px;width:408px;height:105px;background:rgba(255,255,255,.72);padding:18px 28px;font-family:'Poppins',sans-serif;font-weight:600;font-size:29px;line-height:36px;color:#333;text-transform:uppercase}
.dots{left:558px;top:610px;display:flex;gap:11px;align-items:center}
.dots span{width:8px;height:8px;border-radius:50%;background:rgba(255,255,255,.85)}
.dots .on{width:12px;height:12px;border:2px solid #fff;background:transparent}

/* about */
.about{left:0;top:660px;width:1200px;height:530px;background:linear-gradient(90deg,#e7e5e8 0%,#f3f2f4 55%,#f7f6f8 100%)}
.about-art{left:150px;top:700px;width:446px;height:446px;border-radius:50%;background:radial-gradient(circle,#7a6a62 0%,#b3a49b 35%,#d9d6da 65%,#eceaee 100%)}
.about-title{left:660px;top:734px;font-size:30px}
.about-text{left:660px;top:824px;width:400px;font-size:18.5px;line-height:25.7px;color:#333}
.btn-solid{background:var(--plum);color:var(--white);font-family:'Poppins',sans-serif;font-weight:600;display:flex;align-items:center;justify-content:center;text-transform:uppercase}

/* jobs */
.news-title{left:0;width:1200px;top:1248px;text-align:center;font-size:29px}
.job{left:130px;width:939px;height:195px;background:var(--white);box-shadow:0 1px 6px rgba(0,0,0,.16)}
.job-head{height:45px;border-bottom:1px solid var(--line);display:flex;align-items:center;padding:0 14px 0 27px;font-size:12px}
.job-role{font-family:'Poppins',sans-serif;font-weight:600;font-size:13.5px;color:var(--ink);flex:1}
.job-meta{color:var(--muted);margin-left:26px}
.job-body{padding:22px 30px 0;font-size:13.5px;line-height:19.5px;color:#333;height:88px}
.job-actions{padding-left:32px;display:flex;gap:13px}
.btn-outline,.btn-apply{height:30px;display:flex;align-items:center;justify-content:center;font-family:'Poppins',sans-serif;font-weight:500;font-size:11px;text-transform:uppercase}
.btn-outline{width:82px;border:2px solid var(--plum);color:var(--plum)}
.btn-apply{width:79px;background:var(--plum);color:var(--white)}

/* employers */
.employers{left:0;top:2570px;width:1200px;height:508px;background:linear-gradient(90deg,#2c2a2f 0%,#524c55 35%,#3e3a42 60%,#2a282c 100%)}
.emp-title{left:0;width:1200px;top:2615px;text-align:center;color:var(--white);font-size:27px}
.emp-card{top:2731px;width:453px;height:279px;background:rgba(94,80,98,.92);color:var(--white)}
.emp-card h3{position:absolute;left:157px;top:38px;font-family:'Poppins',sans-serif;font-weight:600;font-size:20px;text-transform:uppercase}
.emp-card p{position:absolute;left:157px;top:88px;width:255px;font-size:15px;line-height:19.5px}
.emp-card .emp-icon{position:absolute;left:44px;top:46px}
.btn-white{position:absolute;left:162px;top:205px;width:104px;height:30px;background:var(--white);color:var(--plum);font-family:'Poppins',sans-serif;font-weight:600;font-size:13px;display:flex;align-items:center;justify-content:center}

/* footer */
.footer{left:0;top:3078px;width:1200px;height:405px;background:var(--footer-bg)}
.footer-ring{left:28px;top:3028px;width:340px;height:340px;border-radius:50%;border:26px solid rgba(94,80,98,.05)}
.footer-brand{left:143px;top:3137px;width:210px;height:210px;border-radius:50%;background:var(--plum);border:12px solid #d7dccf}
.footer-brand-name{left:130px;top:3360px;width:236px;text-align:center;font-size:15px;color:var(--plum)}
.foot-h{font-family:'Poppins',sans-serif;font-weight:600;font-size:15px;color:var(--ink)}
.foot-menu{list-style:none;font-size:14px;line-height:24px;color:#333}
.contact-row{display:flex;gap:12px;align-items:flex-start;font-size:14px;line-height:18.5px;color:#333}
.icon-dot{width:28px;height:28px;border-radius:50%;background:var(--plum);flex:none;display:flex;align-items:center;justify-content:center;margin-top:2px}
.foot-divider{left:130px;top:3393px;width:940px;height:1px;background:#d6d3d7}
.copyright{left:0;width:1200px;top:3427px;text-align:center;font-size:11.5px;color:#444}
</style>
</head>
<body>

<!-- Hero -->
<div class="abs hero" role="img" aria-label="Photo of an attorney in a grey suit talking with two colleagues in a bright office"></div>
<div class="abs brand"><div class="brand-dot"></div><span class="brand-name">harborline legal search</span></div>
<nav class="abs nav">
  <a class="active" href="#">HOME</a><a href="#">ABOUT US</a><a href="#">WHAT’S NEW</a><a href="#">FOR EMPLOYERS</a><a href="#">CONTACT US</a>
</nav>
<div class="abs search-btn">
  <svg width="12" height="12" viewBox="0 0 12 12"><circle cx="5" cy="5" r="3.6" fill="none" stroke="#fff" stroke-width="1.6"/><line x1="7.7" y1="7.7" x2="11" y2="11" stroke="#fff" stroke-width="1.8"/></svg>
</div>
<div class="abs hero-caption">Start here, let our experience guide you</div>
<div class="abs dots"><span></span><span></span><span class="on"></span><span></span><span></span></div>

<!-- About -->
<div class="abs about" role="img" aria-label="Faded photo of professionals in a meeting"></div>
<div class="abs about-art" role="img" aria-label="Circular maze decoration revealing a meeting photo"></div>
<h2 class="abs heading about-title">ABOUT US</h2>
<div class="rule" style="left:661px;top:778px;width:52px"></div>
<p class="abs about-text">Harborline Legal Search focuses on the permanent placement of attorneys with law firms and corporations in the New England area. Founded in 1982, Harborline Legal Search is the oldest attorney search firm in New England, and is ranked the number one legal recruiter in New England in the most recent survey conducted by Counsel Quarterly .</p>
<a class="abs btn-solid" style="left:663px;top:1066px;width:122px;height:39px;font-size:15px">Read More</a>

<!-- What's new -->
<h2 class="abs heading news-title">WHAT’S NEW</h2>
<div class="rule" style="left:574px;top:1300px;width:52px"></div>

<article class="abs job" style="top:1357px">
  <div class="job-head"><span class="job-role">IN-HOUSE/CORPORATE/M&amp;A</span><span class="job-meta">Listing Date: 02/10/2020</span><span class="job-meta">Job Id: 2772</span></div>
  <div class="job-body">Global exchange-listed medical technology leader seeks 8+ year M&amp;A specialist with major law firm training for lead role on all M&amp;A and other BD transactions. As a key member of the leadership team, this role will partner with the Vice President.</div>
  <div class="job-actions"><a class="btn-outline">Read More</a><a class="btn-apply">Apply Job</a></div>
</article>

<article class="abs job" style="top:1571px">
  <div class="job-head"><span class="job-role">ASSOCIATE/LITIGATION</span><span class="job-meta">Listing Date: 02/10/2020</span><span class="job-meta">Job Id: 2772</span></div>
  <div class="job-body">Highly regarded mid-size national firm seeks litigation associate with 4-8 years of experience to join their Litigation Practice. This associate will work on a wide array of litigation matters including, construction, real estate, employment, shareholder and general business disputes.</div>
  <div class="job-actions"><a class="btn-outline">Read More</a><a class="btn-apply">Apply Job</a></div>
</article>

<article class="abs job" style="top:1786px">
  <div class="job-head"><span class="job-role">IN-HOUSE/SENIOR CORPORATE COUNSEL/SECURITIES</span><span class="job-meta">Listing Date: 02/10/2020</span><span class="job-meta">Job Id: 2772</span></div>
  <div class="job-body">Leading Cambridge-based publicly traded biotechnology company seeks 10+ year industry-experienced corporate/securities attorney for lead role in all public company matters and ongoing compliance, corporate governance, and corporate financing transactions</div>
  <div class="job-actions"><a class="btn-outline">Read More</a><a class="btn-apply">Apply Job</a></div>
</article>

<article class="abs job" style="top:2000px">
  <div class="job-head"><span class="job-role">IN-HOUSE/BIOTECH/CONTRACTS</span><span class="job-meta">Listing Date: 02/10/2020</span><span class="job-meta">Job Id: 2772</span></div>
  <div class="job-body">Outstanding opportunity for 3+ year attorney to join a premier biotech company in contracts counsel role. Prior experience drafting and negotiating biotech agreements including Clinical Trial Agreements, Master Service Agreements and related research and development contracts is required.</div>
  <div class="job-actions"><a class="btn-outline">Read More</a><a class="btn-apply">Apply Job</a></div>
</article>

<article class="abs job" style="top:2216px">
  <div class="job-head"><span class="job-role">IN-HOUSE/CORPORATE/LIFE SCIENCES TECHNOLOGY INCUBATOR</span><span class="job-meta">Listing Date: 02/10/2020</span><span class="job-meta">Job Id: 2772</span></div>
  <div class="job-body">Leading university research group seeks corporate attorney to serve as lead counsel for their life science technology incubator. Qualified candidates should have 7+ years’ experience in corporate/emerging companies matters, expertise in drafting and negotiating life sciences</div>
  <div class="job-actions"><a class="btn-outline">Read More</a><a class="btn-apply">Apply Job</a></div>
</article>

<a class="abs btn-solid" style="left:521px;top:2457px;width:158px;height:43px;font-size:17px">Search Jobs</a>

<!-- For employers -->
<div class="abs employers" role="img" aria-label="Dark photo of a diverse team collaborating at a table"></div>
<h2 class="abs heading emp-title">FOR EMPLOYERS</h2>
<div class="rule" style="left:574px;top:2668px;width:52px;background:#fff"></div>

<div class="abs emp-card" style="left:130px">
  <svg class="emp-icon" width="70" height="70" viewBox="0 0 70 70" fill="#fff">
    <polygon points="35,4 66,20 4,20"/><rect x="6" y="22" width="58" height="5"/>
    <rect x="12" y="30" width="8" height="26"/><rect x="31" y="30" width="8" height="26"/><rect x="50" y="30" width="8" height="26"/>
    <rect x="6" y="58" width="58" height="4"/><rect x="2" y="64" width="66" height="4"/>
  </svg>
  <h3>Law Firm</h3>
  <p>For over twenty-five years, Harborline Legal Search has partnered with firms of all sizes throughout the New England area to assist with their strategic growth..</p>
  <a class="btn-white">READ MORE</a>
</div>

<div class="abs emp-card" style="left:617px">
  <svg class="emp-icon" width="66" height="72" viewBox="0 0 66 72" fill="#fff">
    <rect x="6" y="2" width="38" height="68"/><rect x="44" y="30" width="18" height="40"/>
    <g fill="#5e5062">
      <rect x="11" y="8" width="7" height="7"/><rect x="22" y="8" width="7" height="7"/><rect x="33" y="8" width="7" height="7"/>
      <rect x="11" y="20" width="7" height="7"/><rect x="22" y="20" width="7" height="7"/><rect x="33" y="20" width="7" height="7"/>
      <rect x="11" y="32" width="7" height="7"/><rect x="22" y="32" width="7" height="7"/><rect x="33" y="32" width="7" height="7"/>
      <rect x="11" y="44" width="7" height="7"/><rect x="33" y="44" width="7" height="7"/><rect x="49" y="38" width="7" height="7"/>
      <rect x="21" y="56" width="9" height="14"/><rect x="49" y="50" width="7" height="7"/>
    </g>
  </svg>
  <h3>In House</h3>
  <p>Founded in 1982, Harborline Legal Search is the premier in-house counsel recruiting firm in the region. We have a proven record of success, working with companies of all sizes...</p>
  <a class="btn-white">READ MORE</a>
</div>

<!-- Footer -->
<footer class="abs footer"></footer>
<div class="abs footer-ring"></div>
<div class="abs footer-brand"></div>
<div class="abs footer-brand-name">harborline legal search</div>

<div class="abs" style="left:433px;top:3124px">
  <h4 class="foot-h">MENU</h4>
  <ul class="foot-menu" style="margin-top:16px">
    <li>HOME</li><li>ABOUT US</li><li>WHAT’S NEW</li><li>FOR EMPLOYERS</li><li>CONTACT US</li>
  </ul>
</div>

<div class="abs" style="left:626px;top:3124px">
  <h4 class="foot-h">CONTACT US</h4>
  <div class="contact-row" style="margin-top:20px">
    <span class="icon-dot"><svg width="10" height="14" viewBox="0 0 10 14"><path d="M5 0a5 5 0 0 1 5 5c0 3.5-5 9-5 9S0 8.5 0 5a5 5 0 0 1 5-5z" fill="#fff"/><circle cx="5" cy="5" r="1.8" fill="#5e5062"/></svg></span>
    <span>P.O. Box 41207,<br>Portland ME 04112</span>
  </div>
  <div class="contact-row" style="margin-top:22px">
    <span class="icon-dot"><svg width="12" height="12" viewBox="0 0 12 12"><path d="M2.5 0.5l2 2.6-1.2 1.4c.8 1.7 2.2 3.1 3.9 3.9l1.4-1.2 2.6 2-1.5 2.3C4.9 11.3.7 7.1.2 2z" fill="#fff"/></svg></span>
    <span>Call Us<br>&nbsp;555.014.2290</span>
  </div>
  <div class="contact-row" style="margin-top:22px">
    <span class="icon-dot"><svg width="13" height="10" viewBox="0 0 13 10"><rect x="0" y="0" width="13" height="10" rx="1" fill="#fff"/><path d="M0.5 0.8l6 4.6 6-4.6" fill="none" stroke="#5e5062" stroke-width="1.2"/></svg></span>
    <span>E mail Us<br>info@harborlinelegal.example</span>
  </div>
</div>

<div class="abs" style="left:944px;top:3124px">
  <h4 class="foot-h">FOLLOW US</h4>
  <div class="contact-row" style="margin-top:20px"><span class="icon-dot"></span><span>Like us on<br>FRIENDLOOP</span></div>
  <div class="contact-row" style="margin-top:24px"><span class="icon-dot"></span><span>Follow us on<br>CHIRPWIRE</span></div>
  <div class="contact-row" style="margin-top:24px"><span class="icon-dot"></span><span>Follow us on<br>PROLINKS</span></div>
</div>

<div class="abs foot-divider"></div>
<p class="abs copyright">Copyright © 2020 All Rights Reserved</p>

</body>
</html>
```